Mindfulness School for Children -- Business Cards

We're looking for business cards for our school directors and owners. We're a mindfulness school for children called little lanterns. Attached are our logos/icons.

```html
<!DOCTYPE html>
<html lang="en">
<head>
<meta charset="utf-8">
<title>little lanterns — Business Cards</title>
<link rel="stylesheet" href="https://fonts.googleapis.com/css2?family=Lora:wght@400&family=Montserrat:wght@400&display=swap">
<style>
  :root {
    --backdrop: #dcdcdc;
    --card-white: #ffffff;
    --wave-blue: #62b6cd;
    --wave-blue-light: #7cc8dd;
    --wave-green: #6fb39a;
    --brand-teal: #4a9fb5;
    --text-white: #ffffff;
    --card-dark: #2a2a2a;
    --dark-name: #4a4a4a;
    --url-grey: #bdbdbd;
  }
  * { margin: 0; padding: 0; box-sizing: border-box; }
  html, body { width: 1200px; height: 800px; overflow: hidden; }
  body {
    background: var(--backdrop);
    display: flex;
    align-items: center;
    justify-content: center;
    gap: 48px;
  }
  .card {
    position: relative;
    width: 540px;
    height: 309px;
    border-radius: 18px;
    overflow: hidden;
    box-shadow: 0 10px 26px rgba(0,0,0,0.18);
  }
  .card--front { background: var(--card-white); }
  .card--back { background: var(--card-dark); }
  .wave { position: absolute; inset: 0; width: 100%; height: 100%; }

  .brand-name {
    position: absolute;
    left: 58px;
    top: 62px;
    font-family: "Lora", serif;
    font-weight: 400;
    font-size: 46px;
    color: var(--brand-teal);
    letter-spacing: 0.5px;
  }
  .person {
    position: absolute;
    left: 40px;
    top: 222px;
    width: 196px;
    text-align: right;
    color: var(--text-white);
  }
  .person__name { font-family: "Lora", serif; font-size: 24px; line-height: 1.1; }
  .person__title { font-family: "Montserrat", sans-serif; font-size: 11px; letter-spacing: 0.6px; }
  .divider {
    position: absolute;
    left: 250px;
    top: 205px;
    width: 1px;
    height: 82px;
    background: rgba(255,255,255,0.6);
  }
  .contact {
    position: absolute;
    left: 264px;
    top: 200px;
    list-style: none;
    font-family: "Montserrat", sans-serif;
    font-size: 11px;
    line-height: 17px;
    color: var(--text-white);
  }
  .contact li { display: flex; align-items: flex-start; gap: 7px; }
  .contact .icon { width: 10px; height: 10px; margin-top: 3px; flex: none; }
  .contact .indent { padding-left: 17px; }

  .back-name {
    position: absolute;
    left: 0; right: 0;
    top: 112px;
    text-align: center;
    font-family: "Lora", serif;
    font-size: 40px;
    color: var(--dark-name);
  }
  .back-url {
    position: absolute;
    right: 34px;
    bottom: 34px;
    font-family: "Montserrat", sans-serif;
    font-size: 11px;
    letter-spacing: 5px;
    color: var(--url-grey);
  }
</style>
</head>
<body>
  <section class="card card--front" aria-label="Business card front">
    <svg class="wave" viewBox="0 0 540 309" preserveAspectRatio="none" aria-hidden="true">
      <defs>
        <linearGradient id="blueBand" x1="0" y1="0" x2="1" y2="1">
          <stop offset="0" stop-color="var(--wave-blue-light)"/>
          <stop offset="1" stop-color="var(--wave-blue)"/>
        </linearGradient>
      </defs>
      <path d="M0,196 C110,138 250,158 350,128 C430,104 466,52 492,0 L540,0 L540,309 L0,309 Z" fill="var(--wave-green)"/>
      <path d="M0,205 C110,147 252,167 354,137 C436,112 472,58 500,0 L540,0 L540,309 L0,309 Z" fill="var(--card-white)"/>
      <path d="M0,210 C112,152 256,172 358,142 C440,117 476,62 505,0 L540,0 L540,309 L0,309 Z" fill="url(#blueBand)"/>
    </svg>

    <div class="brand-name">little lanterns</div>

    <div class="person">
      <div class="person__name">Daniel Reyes</div>
      <div class="person__title">President</div>
    </div>
    <div class="divider"></div>

    <ul class="contact">
      <li>
        <svg class="icon" viewBox="0 0 10 10"><path d="M5,0.5 A3.2,3.2 0 0 1 8.2,3.7 C8.2,6 5,9.5 5,9.5 C5,9.5 1.8,6 1.8,3.7 A3.2,3.2 0 0 1 5,0.5 Z" fill="#fff"/><circle cx="5" cy="3.7" r="1.2" fill="var(--wave-blue)"/></svg>
        <span>1420 Willow Bend Road</span>
      </li>
      <li class="indent">Juneau, Alaska 99801</li>
      <li>
        <svg class="icon" viewBox="0 0 10 10"><path d="M2.2,0.8 L3.8,2.8 L2.9,3.9 C3.6,5.4 4.6,6.4 6.1,7.1 L7.2,6.2 L9.2,7.8 L8.2,9.2 C4.4,9 1,5.6 0.8,1.8 Z" fill="#fff"/></svg>
        <span>555-014-2278</span>
      </li>
      <li>
        <svg class="icon" viewBox="0 0 10 10"><rect x="0.5" y="2" width="9" height="6.5" fill="#fff"/><path d="M0.8,2.3 L5,5.6 L9.2,2.3" fill="none" stroke="var(--wave-blue)" stroke-width="0.9"/></svg>
        <span>hello@littlelanterns.com</span>
      </li>
    </ul>
  </section>

  <section class="card card--back" aria-label="Business card back">
    <div class="back-name">little lanterns</div>
    <div class="back-url">WWW.LITTLELANTERNS.COM</div>
  </section>
</body>
</html>
```